Visitenkarten/Briefpaier/Kassenkassenbelege für Juwelier
Zielgruppe
Mittelständischer Juwelier mit zwei Filialen. Klassischer Schmuck, Uhren und Modeschmuck
Aufgabenstellung
Es müssen für zwei Geschäfte Visitenkarten, Briefpapier (A4) und Kassenkassenbelege (A6) erstellt werden. Logo und Typo im Anhang. Ein Farbkonzept besteht noch nicht. Die Idee geht in Richtung Bordeaux-Rot.
Generell:
(1) Sieht erstmal nach viel Beschreibung aus, bitte nicht entmutigen lassen, sind zu 90% nur austauschbare Inhalts-/Kontaktdaten.
(2) Für meine Zwecke reicht es vollkommen aus, wenn bei den Vorschlägen zur Arbeitsersparnis erstmal nur mit einer Adresse gearbeitet wird. Wenn ich dann den zutreffenden Designvorschlag gefunden habe, können wir die zweite Adresse in dem ersten Format umsetzen. Ich denke das spart Zeit und Nerven.
(3) Bitte Angaben wie "Tel.:" oder "USt.- ID:" nicht wörtlich nehmen, es soll dabei klar sein worum es geht; wenn "Telefon" ausgeschrieben besser aussieht, bitte in der optisch ansprechenderen Form verwenden.
(4) Bei Fragen, bitte fragen!
(5) Viel Spass bei dem Projekt - Ich freu' mich auf die Vorschläge!
Visitenkarten(1):
Juwelier Brenneck GmbH
www.juwelier-brenneck-beispiel.de
Visitenkarten(2):
Visitenkarten(generell):
(1) Die einzelnen Daten können durch Hervorhebungen wie Adresse, Kontakt, Online/Internet unterteilt bzw. hervorgehoben werden.
(2) Die Visitenkarten sollen farbig gedruckt werden; geplant ist weiß als Hintergrund ist aber nicht zwingend bei einer guten anderen Idee
Briefpapier:
(1)Absender im Adressfeld für DIN-lang Briefumschläge mit Fenster:
(2)Informationen im Footer/Seitenbereich:
Juwelier Brenneck Gmb..

```html
<!DOCTYPE html>
<html lang="de">
<head>
<meta charset="utf-8">
<title>Juwelier Brenneck – Geschäftsausstattung</title>
<link href="https://fonts.googleapis.com/css2?family=Source+Sans+3:wght@300;400;600;700&display=swap" rel="stylesheet">
<style>
  :root {
    --plum: #4a1748;
    --plum-deep: #3f1340;
    --paper-top: #ffffff;
    --paper-bottom: #d6d6d6;
    --tab: #8a8a8a;
    --ink: #3a3a3a;
    --muted: #8b8b8b;
    --placeholder: #e9e2ea;
  }
  * { margin: 0; padding: 0; box-sizing: border-box; }
  html, body { width: 872px; height: 1200px; overflow: hidden; }
  body {
    background: linear-gradient(180deg, var(--plum) 0%, var(--plum-deep) 100%);
    font-family: "Source Sans 3", sans-serif;
    font-weight: 400;
    color: var(--ink);
    position: relative;
  }
  .abs { position: absolute; }

  /* Brand lockup */
  .brand { position: absolute; left: 0; right: 0; text-align: center; }
  .brand-square { display: block; margin: 0 auto; background: var(--plum); }
  .brand-name { display: block; font-weight: 600; color: var(--plum); letter-spacing: 0.02em; white-space: nowrap; }
  .brand.on-dark .brand-square { background: #fff; }
  .brand.on-dark .brand-name { color: #fff; }

  .poster-brand { top: 40px; }
  .poster-brand .brand-square { width: 50px; height: 50px; }
  .poster-brand .brand-name { font-size: 25px; margin-top: 36px; letter-spacing: 0.03em; }

  .sheet {
    position: absolute;
    background: linear-gradient(180deg, var(--paper-top) 0%, var(--paper-bottom) 100%);
  }
  .tab { position: absolute; bottom: 0; background: var(--tab); }
  .label { color: var(--muted); }

  /* Receipt (A6) */
  .receipt { left: 91px; top: 286px; width: 219px; height: 320px; }
  .receipt .brand { top: 11px; }
  .receipt .brand-square { width: 26px; height: 26px; }
  .receipt .brand-name { font-size: 9px; margin-top: 13px; }
  .receipt-image { left: 18px; top: 86px; width: 182px; height: 159px; background: var(--placeholder); }
  .receipt-note, .receipt-contact { left: 0; right: 0; text-align: center; font-size: 4.3px; line-height: 7.5px; color: var(--plum); }
  .receipt-note { top: 254px; }
  .receipt-contact { top: 274px; }
  .receipt .tab { left: 102px; width: 16px; height: 8px; }

  /* Business cards */
  .card { width: 177px; height: 119px; top: 286px; }
  .card .brand { top: 10px; }
  .card .brand-square { width: 28px; height: 28px; }
  .card .brand-name { font-size: 11px; margin-top: 16px; }
  .card .tab { left: 78px; width: 20px; height: 10px; }
  .card-front { left: 337px; }
  .card-dark { left: 535px; width: 178px; background: var(--plum); border: 1px solid #fff; }
  .card-dark .tab { background: #fff; }
  .card-back { left: 129px; top: 627px; }
  .card-back .brand { top: 6px; }
  .card-back .brand-square { width: 26px; height: 26px; }
  .card-back .brand-name { font-size: 9.5px; margin-top: 9px; }
  .card-back-contact { left: 0; right: 0; top: 73px; text-align: center; font-size: 4.4px; line-height: 7.8px; color: var(--plum); }

  /* Letterhead (A4) */
  .letter { left: 337px; top: 428px; width: 438px; height: 643px; font-size: 6.8px; }
  .letter .brand { top: 14px; }
  .letter .brand-square { width: 28px; height: 28px; }
  .letter .brand-name { font-size: 11.5px; margin-top: 24px; }
  .sender-line { left: 50px; top: 106px; font-size: 3.8px; color: var(--plum); }
  .recipient { left: 50px; top: 128px; line-height: 9px; font-style: normal; }
  .recipient .name { font-weight: 600; }
  .branch-info { left: 302px; top: 138px; font-size: 4.4px; line-height: 8.3px; color: var(--plum); }
  .subject { left: 50px; top: 211px; font-weight: 600; text-transform: uppercase; }
  .date { left: 302px; top: 211px; }
  .fold-mark { left: 11px; width: 20px; height: 0.7px; background: #999; }
  .fold-mark.first { top: 226px; }
  .fold-mark.second { top: 453px; }
  .letter-body { left: 50px; top: 238px; width: 340px; line-height: 12.7px; font-weight: 300; color: #333; }
  .letter-body p { text-align: justify; margin-bottom: 12.7px; }
  .letter-footer { left: 0; right: 0; top: 605px; text-align: center; font-size: 4.2px; line-height: 8.2px; color: var(--plum); }
  .letter .tab { left: 209px; width: 21px; height: 10px; }
</style>
</head>
<body>

  <header class="brand poster-brand on-dark">
    <span class="brand-square"></span>
    <span class="brand-name">JUWELIER BRENNECK</span>
  </header>

  <section class="sheet receipt">
    <div class="brand">
      <span class="brand-square"></span>
      <span class="brand-name">JUWELIER BRENNECK</span>
    </div>
    <div class="abs receipt-image" role="img" aria-label="Platz für den Kassenbeleg"></div>
    <p class="abs receipt-note">Bei Umtausch oder Reklamation bitte Beleg vorlegen.<br>Barauszahlung ganz oder teilweise ausgeschlossen.</p>
    <p class="abs receipt-contact">
      <span class="label">JUWELIER BRENNECK GmbH</span><br>
      Am Uhrturm 14 in 12340 Erlenstadt <span class="label">TEL</span> 01111-123450 <span class="label">FAX</span> 01111-123459<br>
      info@juwelier-brenneck-beispiel.de &nbsp;www.juwelier-brenneck-beispiel.de
    </p>
    <span class="tab"></span>
  </section>

  <section class="sheet card card-front">
    <div class="brand">
      <span class="brand-square"></span>
      <span class="brand-name">JUWELIER BRENNECK</span>
    </div>
    <span class="tab"></span>
  </section>

  <section class="abs card card-dark">
    <div class="brand on-dark">
      <span class="brand-square"></span>
      <span class="brand-name">JUWELIER BRENNECK</span>
    </div>
    <span class="tab"></span>
  </section>

  <section class="sheet card card-back">
    <div class="brand">
      <span class="brand-square"></span>
      <span class="brand-name">JUWELIER BRENNECK</span>
    </div>
    <p class="abs card-back-contact">
      <span class="label">JUWELIER BRENNECK GmbH</span><br>
      Am Uhrturm 14 in 12340 Erlenstadt<br>
      <span class="label">TEL</span> 01111-123450 &nbsp;<span class="label">FAX</span> 01111-123459 &nbsp;info@juwelier-brenneck-beispiel.de<br>
      www.juwelier-brenneck-beispiel.de
    </p>
    <span class="tab"></span>
  </section>

  <section class="sheet letter">
    <div class="brand">
      <span class="brand-square"></span>
      <span class="brand-name">JUWELIER BRENNECK</span>
    </div>

    <p class="abs sender-line"><span class="label">JUWELIER BRENNECK GmbH</span> &nbsp;Am Uhrturm 14 &nbsp;<span class="label">12340</span> Erlenstadt</p>

    <address class="abs recipient">
      Frau<br>
      <span class="name">Marlene Saphir</span><br>
      Opalweg 22<br><br>
      12340 Erlenstadt
    </address>

    <p class="abs branch-info">
      <span class="label">Filiale Erlenstadt:</span><br>
      <span class="label">TEL</span> 01111-123450 &nbsp;<span class="label">FAX</span> 01111-123459<br>
      <span class="label">Filiale Weidenhain:</span><br>
      <span class="label">TEL</span> 01122-555010 &nbsp;<span class="label">FAX</span> 01122-555019<br>
      info@juwelier-brenneck-beispiel.de<br>
      www.juwelier-brenneck-beispiel.de
    </p>

    <p class="abs subject">Diamantstaub am Horizont</p>
    <p class="abs date">Erlenstadt, den 03. 05. 2014</p>

    <span class="abs fold-mark first"></span>
    <span class="abs fold-mark second"></span>

    <div class="abs letter-body">
      <p>Sehr geehrte Frau Saphir,</p>
      <p>hier schreibe ich einen Blindtext dahin: Diamanten, die groß genug für die Schmuckproduktion sind, bilden sich nur im Erdmantel unter hohen Drücken und Temperaturen, typischerweise in Tiefen zwischen 150 bis 660 Kilometern[4] und bei Temperaturen von 1200 bis 1400 °C. Diamant-Muttergesteine im Erdmantel sind Peridotit und Eklogit. Letzterer kann versenkte ozeanische Kruste repräsentieren.</p>
      <p>Die jeweilige Transportdauer aus der Tiefe wird auf wenige Stunden geschätzt, sodass aufgrund der Schnelligkeit keine Phasenumwandlung zu Graphit stattfindet. Die letzte Phase der Eruption erfolgt mit Überschallgeschwindigkeit. Diamanten sind Fremd- oder Xenokristalle in Kimberlit und Lamproit und in diesen Magmen chemisch nicht stabil (metastabil).</p>
      <p>So kann man an natürlichen Diamanten immer Auflösungserscheinungen beobachten. Von ihren Vorkommen in Pipes können die Diamantkristalle durch natürliche Verwitterungsprozesse, bei denen sie aufgrund ihrer Härte intakt bleiben, abtransportiert und in Sedimentgesteinen angereichert werden, die heute eine der Hauptquellen dieses Minerals darstellen.</p>
      <p>Mit den allerbesten Grüßen</p>
      <p>Greta Topas</p>
    </div>

    <footer class="abs letter-footer">
      <span class="label">Juwelier Brenneck GmbH</span> &nbsp;Am Uhrturm 14 in 12340 Erlenstadt &nbsp;<span class="label">Filiale</span> Bergstraße 8 in 12350 Weidenhain<br>
      <span class="label">Geschäftsführer</span> Renate Brenneck &nbsp;<span class="label">Amtsgericht Erlenstadt</span> HRB 00000 &nbsp;<span class="label">Steuernummer</span> 000/0000/0000 &nbsp;<span class="label">USt.- ID</span> DE 000000000<br>
      <span class="label">Bank</span> Musterbank AG &nbsp;<span class="label">IBAN</span> DE00 0000 0000 0000 0000 00 &nbsp;<span class="label">BIC</span> MUST DE 00
    </footer>

    <span class="tab"></span>
  </section>

</body>
</html>
```